Business Card Design

New business card design

Target Market(s)

Residential & Commercial Property Managers

Industry/Entity Type

Plumbing Services

Contact Information for Business Card

Name - Rowan Keddle, title - Director, Phone Number - 0431 286 517, email - rowan@tbk-plumbing.com.au, Company ABN - 73 215 904 386,

Font styles to use
Sans Serif

Colors
0054AA
0677BA
7BADD7
CADEEF
E8F1F8

```html
<!DOCTYPE html>
<html lang="en">
<head>
<meta charset="utf-8">
<title>TBK Plumbing Services – Business Card</title>
<link rel="stylesheet" href="https://fonts.googleapis.com/css2?family=Montserrat:wght@400;500;600;700&display=swap">
<style>
  :root {
    --page-bg: #1e1f21;
    --card-dark: #141414;
    --card-light: #ffffff;
    --ink: #1b2530;
    --ink-soft: #6e6660;
    --brand-blue: #1a9ad6;
    --name-dark: #3a3a3a;
    --rule: #2a2f35;
  }
  * { box-sizing: border-box; margin: 0; padding: 0; }
  html, body {
    width: 1200px; height: 1200px; overflow: hidden;
    background: var(--page-bg);
    font-family: "Montserrat", sans-serif;
  }
  .canvas {
    width: 1200px; height: 1200px;
    display: flex; flex-direction: column; align-items: center; justify-content: center;
    gap: 44px;
  }
  .card {
    position: relative;
    width: 860px; height: 526px;
    border-radius: 30px;
    overflow: hidden;
  }
  .card--back { background: var(--card-dark); }
  .card--front { background: var(--card-light); }

  .company-name {
    position: absolute;
    font-weight: 600;
    line-height: 1.15;
  }
  .card--back .company-name {
    left: 50%; top: 50%; transform: translate(-50%, -50%);
    width: 640px; text-align: center;
    font-size: 52px; color: var(--name-dark);
  }
  .card--front .company-name {
    left: 64px; top: 212px; width: 310px;
    font-size: 38px; color: var(--ink);
  }

  .divider {
    position: absolute; left: 410px; top: 178px;
    width: 2px; height: 164px; background: var(--rule);
  }
  .contact {
    position: absolute; left: 440px; top: 176px;
    color: var(--ink);
  }
  .contact__name {
    font-size: 29px; font-weight: 700; color: var(--brand-blue);
    text-transform: uppercase; line-height: 1.05;
  }
  .contact__title { font-size: 19px; color: var(--ink-soft); margin-bottom: 12px; }
  .contact__line {
    display: flex; align-items: center; gap: 10px;
    font-size: 20px; font-weight: 500; line-height: 1.55;
  }
  .contact__line svg { width: 18px; height: 18px; flex: none; }
  .contact__line--plain { padding-left: 28px; }

  .band { position: absolute; bottom: 0; height: 16px; }
  .band--dark { left: 0; width: 58%; background: var(--ink); }
  .band--blue { left: calc(58% + 6px); right: 0; background: var(--brand-blue); }
</style>
</head>
<body>
<main class="canvas">
  <section class="card card--back" aria-label="Card back">
    <p class="company-name">TBK Plumbing Services</p>
  </section>

  <section class="card card--front" aria-label="Card front">
    <p class="company-name">TBK Plumbing Services</p>

    <div class="divider"></div>

    <div class="contact">
      <p class="contact__name">Rowan Keddle</p>
      <p class="contact__title">Director</p>
      <p class="contact__line">
        <svg viewBox="0 0 24 24" aria-hidden="true"><path fill="#1a9ad6" d="M6.6 10.8a15.2 15.2 0 0 0 6.6 6.6l2.2-2.2a1 1 0 0 1 1-.25 11.4 11.4 0 0 0 3.6.6 1 1 0 0 1 1 1V20a1 1 0 0 1-1 1A17 17 0 0 1 3 4a1 1 0 0 1 1-1h3.5a1 1 0 0 1 1 1c0 1.25.2 2.45.6 3.6a1 1 0 0 1-.25 1z"/></svg>
        0431 286 517
      </p>
      <p class="contact__line">
        <svg viewBox="0 0 24 24" aria-hidden="true"><rect x="2" y="5" width="20" height="14" rx="2" fill="#1a9ad6"/><path d="M3 6.5l9 6.5 9-6.5" fill="none" stroke="#fff" stroke-width="1.8"/></svg>
        rowan@tbk-plumbing.com.au
      </p>
      <p class="contact__line contact__line--plain">ABN: 73 215 904 386</p>
    </div>

    <div class="band band--dark"></div>
    <div class="band band--blue"></div>
  </section>
</main>
</body>
</html>
```